Business Card for a mobile physiotherapy company

I need a layout for a business card for a mobile physiotherapy company.
Slogan is "Mobile Physiotherapy - Your Road To Recovery"
Phone number is 867-555-0142
Email VardenTherapy@postnest.ca (subject to change with website)
Website www.VardenTherapy.ca
My name and credentials: Luke Varden Luke Varden, BSc(kin), MPT, CAFCI, IMS
Information maybe included: Direct Billing, Services including Physiotherapy, IMS, acupuncture
Maybe include facebook and instagram logos
One side with the logo clean and sharp
Other side with details, try not to look too busy, keep everything concise

```html
<!DOCTYPE html>
<html lang="en">
<head>
<meta charset="utf-8">
<title>Varden Therapy – Business Card</title>
<link href="https://fonts.googleapis.com/css2?family=Roboto:ital,wght@0,400;0,500;0,700;1,400&display=swap" rel="stylesheet">
<style>
  :root {
    --page-bg: #e6e6e6;
    --card-white: #fafafa;
    --navy: #2c4a72;
    --green: #0d5a45;
    --text-grey: #555a60;
    --divider: #9a9a9a;
    --white: #ffffff;
  }
  html, body {
    margin: 0;
    padding: 0;
    width: 1125px;
    height: 1200px;
    overflow: hidden;
    background: var(--page-bg);
    font-family: "Roboto", Arial, sans-serif;
  }
  .canvas {
    position: relative;
    width: 1125px;
    height: 1200px;
  }
  .card {
    position: absolute;
    left: 171px;
    width: 826px;
    height: 472px;
  }
  .card-front {
    top: 106px;
    background: var(--card-white);
  }
  .card-back {
    top: 639px;
    background: var(--navy);
  }

  /* Front */
  .brand-front {
    position: absolute;
    left: 60px;
    top: 178px;
    width: 345px;
    text-align: center;
    color: var(--navy);
    font-weight: 700;
    font-size: 44px;
    line-height: 1.1;
    letter-spacing: 1px;
  }
  .divider {
    position: absolute;
    left: 393px;
    top: 136px;
    width: 2px;
    height: 208px;
    background: linear-gradient(to bottom, transparent, var(--divider) 20%, var(--divider) 80%, transparent);
  }
  .details {
    position: absolute;
    left: 441px;
    top: 145px;
  }
  .person-name {
    margin: 0;
    font-size: 30px;
    font-weight: 700;
    color: var(--navy);
    line-height: 34px;
    letter-spacing: 0.3px;
  }
  .credentials {
    margin: 0;
    font-size: 19px;
    font-weight: 500;
    color: var(--navy);
    line-height: 24px;
  }
  .billing {
    margin: 2px 0 0;
    font-size: 21px;
    font-weight: 500;
    color: var(--green);
    line-height: 26px;
  }
  .contact-list {
    list-style: none;
    margin: 14px 0 0;
    padding: 0;
  }
  .contact-list li {
    display: flex;
    align-items: center;
    font-size: 19.5px;
    color: var(--text-grey);
    line-height: 26.5px;
  }
  .contact-list svg {
    width: 17px;
    height: 17px;
    margin-right: 13px;
    fill: var(--navy);
    flex: none;
  }

  /* Back */
  .social-badges {
    position: absolute;
    top: 42px;
    right: 50px;
    display: flex;
    gap: 4px;
  }
  .social-badges span {
    width: 38px;
    height: 38px;
    border-radius: 50%;
    background: var(--white);
  }
  .brand-back {
    position: absolute;
    left: 0;
    right: 0;
    top: 170px;
    text-align: center;
    color: var(--white);
    font-weight: 700;
    font-size: 54px;
    letter-spacing: 2px;
  }
  .slogan {
    position: absolute;
    left: 0;
    right: 0;
    top: 378px;
    margin: 0;
    text-align: center;
    color: var(--white);
    font-style: italic;
    font-size: 19.5px;
  }
  .services {
    position: absolute;
    left: 0;
    right: 0;
    top: 407px;
    margin: 0;
    text-align: center;
    color: var(--white);
    font-size: 19.5px;
  }
</style>
</head>
<body>
<main class="canvas">
  <section class="card card-front">
    <div class="brand-front">VARDEN<br>THERAPY</div>
    <div class="divider"></div>
    <div class="details">
      <h1 class="person-name">LUKE VARDEN</h1>
      <p class="credentials">BSc(kin), MPT, CAFCI, IMS</p>
      <p class="billing">Direct Billing</p>
      <ul class="contact-list">
        <li>
          <svg viewBox="0 0 24 24" aria-hidden="true"><path d="M6.6 10.8a15.1 15.1 0 0 0 6.6 6.6l2.2-2.2a1 1 0 0 1 1-.25 11.4 11.4 0 0 0 3.6.57 1 1 0 0 1 1 1V20a1 1 0 0 1-1 1A17 17 0 0 1 3 4a1 1 0 0 1 1-1h3.5a1 1 0 0 1 1 1c0 1.25.2 2.45.57 3.57a1 1 0 0 1-.25 1z"/></svg>
          867-555-0142
        </li>
        <li>
          <svg viewBox="0 0 24 24" aria-hidden="true"><path d="M2 5h20v14H2z M4 7v.5l8 5 8-5V7l-8 5z" fill-rule="evenodd"/></svg>
          VardenTherapy@postnest.ca
        </li>
        <li>
          <svg viewBox="0 0 24 24" aria-hidden="true"><circle cx="12" cy="12" r="10"/><path d="M7 8c2 0 3 1 3 3s2 2 2 4-1 3 0 4M14 4c0 2 2 2 3 3s3 1 4 0" stroke="#fafafa" stroke-width="1.6" fill="none"/></svg>
          www.VardenTherapy.ca
        </li>
      </ul>
    </div>
  </section>

  <section class="card card-back">
    <div class="social-badges" aria-hidden="true"><span></span><span></span></div>
    <div class="brand-back">VARDEN THERAPY</div>
    <p class="slogan">Mobile Physiotherapy - Your Road To Recovery</p>
    <p class="services">Physiotherapy • IMS • Acupuncture</p>
  </section>
</main>
</body>
</html>
```